Small Business Consulting Firm Needs Letterhead

We need a letterhead for our company "Brightpath Plus". Our company does outbound calling and mailing to business owner's companies who have taken high interest loans. These loans tend to put these businesses in a big financial bind short term, and we help them find better financial options. We would like the design to match our colors of our logo. Headers and footers would look nice, but we are open. We would want it to include our address, website, phone, and email info. Our address - 2000 E. Lamar Blvd. Suite 600Website - www.safeguardtoday.comEmail - info@safeguardtoday.comPhone - 855-726-1938
Industry/Entity Type
Financial Planning
Look and feel
Each slider illustrates characteristics of the customer's brand and the style your logo design should communicate.

```html
<!DOCTYPE html>
<html lang="en">
<head>
<meta charset="utf-8">
<title>Brightpath Plus Letterhead</title>
<link href="https://fonts.googleapis.com/css2?family=Lato:wght@400;700&family=Montserrat:wght@400&display=swap" rel="stylesheet">
<style>
  :root {
    --green: #7aba43;
    --blue: #1a7fc3;
    --ink: #2b2b2b;
    --grey-text: #555a5e;
    --backdrop: #e4e4e4;
    --paper: #ffffff;
  }
  * { margin: 0; padding: 0; box-sizing: border-box; }
  html, body { width: 1200px; height: 1200px; overflow: hidden; }
  body {
    background: var(--backdrop);
    font-family: "Lato", sans-serif;
    color: var(--ink);
    position: relative;
  }
  .letterhead {
    position: absolute;
    left: 216px; top: 103px;
    width: 768px; height: 994px;
    background: var(--paper);
    box-shadow: 0 3px 10px rgba(0,0,0,0.18);
    overflow: hidden;
  }
  .header-wave { position: absolute; left: 0; top: 0; width: 768px; height: 180px; }
  .brand {
    position: absolute; left: 40px; top: 78px;
    display: flex; flex-direction: column; align-items: center; gap: 10px;
  }
  .brand-mark { width: 40px; height: 40px; background: var(--green); }
  .brand-name {
    font-family: "Montserrat", sans-serif; font-weight: 400;
    font-size: 15px; letter-spacing: 1.2px; color: var(--grey-text);
    text-transform: uppercase;
  }
  .letter-date {
    position: absolute; right: 44px; top: 216px;
    font-size: 9px; color: var(--ink);
  }
  .letter-date strong { font-weight: 700; }
  .letter-body { position: absolute; left: 42px; top: 273px; width: 684px; }
  .salutation { font-size: 10.5px; font-weight: 700; color: var(--blue); margin-bottom: 18px; }
  .letter-body p.copy {
    font-size: 8.4px; line-height: 12.5px; text-align: justify; margin-bottom: 12.5px;
  }
  .closing { position: absolute; left: 42px; top: 668px; font-size: 9.5px; font-weight: 700; }
  .signature {
    position: absolute; left: 42px; top: 693px; width: 168px; height: 52px;
    background: linear-gradient(90deg, #ececec, #f7f7f7);
    border-radius: 2px;
  }
  .contact-line {
    position: absolute; left: 42px; top: 940px;
    display: flex; gap: 18px; font-size: 8.4px; color: var(--ink);
  }
  .contact-item { display: flex; align-items: center; gap: 6px; }
  .contact-item svg { width: 9px; height: 9px; fill: var(--blue); }
  .footer-band { position: absolute; left: 0; bottom: 0; width: 768px; height: 36px; }
  .footer-address {
    position: absolute; right: 44px; bottom: 10px;
    display: flex; align-items: center; gap: 7px;
    color: #fff; font-size: 11px; letter-spacing: 0.3px;
  }
  .footer-address svg { width: 10px; height: 13px; fill: #fff; }
</style>
</head>
<body>
<main class="letterhead">
  <svg class="header-wave" viewBox="0 0 768 180" preserveAspectRatio="none" aria-hidden="true">
    <path d="M0 0 H768 V40 C600 18 340 10 0 20 Z" fill="var(--green)"/>
    <path d="M0 30 C300 14 560 40 768 170 V172 C560 52 300 26 0 38 Z" fill="var(--green)"/>
    <path d="M0 0 H768 V172 C690 120 620 60 520 36 C420 14 200 10 0 20 Z" fill="none"/>
    <path d="M300 10 C520 20 680 70 768 168 V40 C640 18 480 8 300 10 Z" fill="var(--green)"/>
  </svg>

  <div class="brand">
    <div class="brand-mark"></div>
    <div class="brand-name">Brightpath Plus</div>
  </div>

  <div class="letter-date"><strong>Date:</strong> 24, August, 2019</div>

  <section class="letter-body">
    <p class="salutation">Dear Daniel Harper,</p>
    <p class="copy">Lorem ipsum dolor sit amet, consectetur adipiscing elit. Curabitur a arcu sagittis, convallis dolor a, gravida lectus. Duis efficitur ipsum ut aliquet scelerisque. Suspendisse eu fermentum metus. Suspendisse ac hendrerit elit. Sed gravida augue tellus, vitae facilisis sapien sodales ac. Curabitur a justo vel lectus tincidunt lobortis eu in lorem. Cras facilisis massa et malesuada sagittis. Aliquam vel nulla aliquet, sollicitudin lorem eget, cursus ligula. Donec a diam facilisis, consectetur ipsum in, posuere tellus. Donec non eros semper, rhoncus dolor ac, auctor elit. In euismod ultrices nisi, vitae volutpat lectus gravida quis. Aliquam accumsan ipsum a nisl volutpat blandit. Praesent venenatis risus a molestie placerat. Ut sagittis mauris non tincidunt fringilla. Sed consectetur diam nec enim gravida, vel gravida mauris aliquam.</p>
    <p class="copy">Pellentesque sit amet nisi viverra, mollis ex at, convallis lacus. Curabitur aliquet vitae arcu vel convallis. Aenean et dictum libero. Mauris tellus nibh, venenatis ac felis sed, vehicula efficitur lectus. Curabitur et ipsum turpis. Ut laoreet maximus viverra. Nunc accumsan velit sit amet lacinia hendrerit. Quisque facilisis nisi at fringilla pretium. Aliquam justo nulla, aliquam et risus at, porttitor pulvinar est. Nam volutpat rutrum venenatis. Praesent tempus nibh risus.</p>
    <p class="copy">Aliquam posuere massa a magna rutrum, id cursus eros viverra. Proin dignissim nunc in mauris tempus, in consequat lacus ultrices. Morbi bibendum non leo sed faucibus. Aliquam pharetra elit in maximus consectetur. In cursus tristique ornare. Nam facilisis sapien in ante tempor consectetur vitae at augue. Proin posuere in massa vitae finibus. Nullam sit amet posuere urna, quis fermentum mi. Pellentesque vel quam in enim tempor venenatis ac ac ligula. Praesent imperdiet euismod elit non ultrices. Pellentesque sed orci et sapien tempus laoreet. Vestibulum felis enim, vestibulum sit amet enim eget, sagittis consectetur neque.</p>
    <p class="copy">Curabitur quam leo, pharetra nec porttitor quis, blandit at orci. Nunc a augue cursus, mollis felis quis, fringilla neque. Proin non augue id lectus tempor lacinia et efficitur elit. Ut scelerisque nibh interdum, hendrerit erat at, pellentesque diam. Sed et venenatis elit, quis mattis metus. Donec rhoncus non ante id commodo. Maecenas commodo non ex sit amet fermentum. Maecenas volutpat, neque at bibendum ullamcorper, odio diam convallis urna, nec pharetra neque justo sit amet orci. Proin et tellus tellus. Praesent ultricies dolor lacinia venenatis dapibus. Proin pharetra bibendum nisl, at congue nibh tincidunt efficitur. Sed egestas eget tellus iaculis mollis.</p>
    <p class="copy">Cras tincidunt ornare lectus, eget sodales ex varius ac. Nunc luctus sollicitudin nisi. Quisque quis dictum ex. Quisque iaculis, tortor porta sagittis blandit, erat leo dapibus nisi, varius gravida mi libero vel lacus. Proin a viverra diam, eu ultrices leo. Curabitur vel ipsum a erat sodales placerat. Etiam eu consectetur augue.</p>
  </section>

  <p class="closing">Sincerely Your,</p>
  <div class="signature" role="img" aria-label="Handwritten signature"></div>

  <div class="contact-line">
    <span class="contact-item">
      <svg viewBox="0 0 10 10" aria-hidden="true"><path d="M2 0.5 L3.6 2.6 L2.7 3.7 C3.3 5 4.9 6.6 6.3 7.3 L7.4 6.4 L9.5 8 L8.3 9.5 C4.4 9.3 0.7 5.6 0.5 1.7 Z"/></svg>
      855-726-1938
    </span>
    <span class="contact-item">
      <svg viewBox="0 0 10 10" aria-hidden="true"><path d="M0.5 2 H9.5 V8 H0.5 Z M1.2 2.5 L5 5.3 L8.8 2.5" stroke="#fff" stroke-width="0.8"/></svg>
      info@brightpathplus.com
    </span>
    <span class="contact-item">
      <svg viewBox="0 0 10 10" aria-hidden="true"><circle cx="5" cy="5" r="4.5"/><path d="M0.5 5 H9.5 M5 0.5 C2.8 3 2.8 7 5 9.5 M5 0.5 C7.2 3 7.2 7 5 9.5" stroke="#fff" stroke-width="0.7" fill="none"/></svg>
      www.brightpathplus.com
    </span>
  </div>

  <svg class="footer-band" viewBox="0 0 768 36" preserveAspectRatio="none" aria-hidden="true">
    <rect x="0" y="14" width="390" height="5" fill="var(--green)"/>
    <rect x="0" y="21" width="390" height="15" fill="var(--paper)"/>
    <rect x="0" y="22" width="390" height="4" fill="var(--blue)"/>
    <path d="M408 0 H768 V36 H380 Z" fill="var(--blue)"/>
  </svg>
  <div class="footer-address">
    <svg viewBox="0 0 10 13" aria-hidden="true"><path d="M5 0 C2.2 0 0 2.2 0 4.9 C0 8.4 5 13 5 13 C5 13 10 8.4 10 4.9 C10 2.2 7.8 0 5 0 Z M5 6.8 A1.9 1.9 0 1 1 5 3 A1.9 1.9 0 1 1 5 6.8 Z"/></svg>
    4170 W. Corwin Ave. Suite 310
  </div>
</main>
</body>
</html>
```